Menu Edit

Hello. We need a pricing edit on our current menu and new logo swapped (we already have the new logo), as well as colour changes. Also, we require a takeaway menu, in-store menu and footpath a-frame edit as well. I have attached the files bellow.

```html
<!DOCTYPE html>
<html lang="en">
<head>
<meta charset="utf-8">
<title>Hook &amp; Harbour — Menu Set</title>
<link rel="stylesheet" href="https://fonts.googleapis.com/css2?family=Montserrat:wght@700;800&family=Roboto+Slab:wght@300;400;700&family=Saira+Semi+Condensed:wght@600;700&display=swap">
<style>
:root{
  --paper:#ffffff;
  --ink:#272324;
  --blue:#1b8fe8;
  --button:#0e8ef0;
  --white:#ffffff;
  --soft:#e6e6e6;
  --rule:#9a9697;
  --tile-green:#1fbf6a;
  --tile-yellow:#ffd21f;
  --tile-teal:#22c6b8;
  --tile-orange:#ff8a00;
  --tile-red:#ff3a12;
  --serif:"Roboto Slab", Georgia, serif;
  --head:"Saira Semi Condensed", "Arial Narrow", sans-serif;
  --bold:"Montserrat", Arial, sans-serif;
}
*{box-sizing:border-box;margin:0;padding:0}
html,body{width:1200px;height:2621px;overflow:hidden;background:var(--paper)}
body{position:relative;font-family:var(--serif);color:var(--white)}
.panel{position:absolute;background:var(--ink);box-shadow:7px 7px 9px rgba(0,0,0,.38)}
.panel > *{position:absolute}
.centered{left:0;right:0;text-align:center}

/* brand lockup */
.brand{display:flex;align-items:center;justify-content:center;gap:14px;left:0;right:0}
.brand-dot{width:22px;height:22px;border-radius:50%;background:var(--blue)}
.brand-name{font-family:var(--serif);font-weight:300;text-transform:uppercase;letter-spacing:1px;white-space:nowrap;color:var(--white)}

/* shared pieces */
.btn{background:var(--button);color:var(--white);font-family:var(--serif);font-weight:700;text-transform:uppercase;text-align:center;border-radius:3px;letter-spacing:.3px}
.phone{display:flex;align-items:center;justify-content:center;gap:10px;font-family:var(--bold);font-weight:800;letter-spacing:1px;white-space:nowrap}
.phone svg{fill:var(--white)}
.web{display:flex;align-items:center;justify-content:center;gap:6px;white-space:nowrap}
.tiles{display:flex;gap:4px}
.tile{height:100%;border-radius:1px}
.tile.green{background:var(--tile-green)}
.tile.yellow{background:var(--tile-yellow)}
.tile.teal{background:var(--tile-teal)}
.tile.orange{background:var(--tile-orange);border-radius:2px}
.tile.red{background:var(--tile-red);border-radius:2px}
.blue{color:var(--blue)}

/* A-frame: hours */
.aframe-hours{left:127px;top:96px;width:445px;height:661px}
.aframe-hours .brand{top:54px}
.aframe-hours .brand-name{font-size:28px}
.welcome{top:176px;font-size:12px;letter-spacing:6px;color:var(--blue)}
.open-title{top:216px;font-size:37px;font-weight:700}
.hours{font-size:21px;font-weight:300;white-space:nowrap}
.hours .blue{margin-right:10px}
.hours.lunch{top:272px}
.hours.dinner{top:297px}
.services{top:334px;font-size:18px;font-weight:300;line-height:23px;text-transform:uppercase}
.services .pipe{color:var(--blue)}
.byo{top:419px;font-size:13px;font-weight:300}
.blue-rule{left:35px;width:375px;height:3px;background:var(--blue)}
.blue-rule.first{top:442px}
.blue-rule.second{top:494px}
.prep{top:451px;font-size:14px;font-weight:300;line-height:19px}
.aframe-hours .phone{top:522px;left:0;right:0;font-size:48px}
.url-pill{left:63px;top:592px;width:320px;height:31px;border-radius:6px;background:var(--button);font-family:var(--bold);font-weight:700;font-size:18px;text-align:center;line-height:31px;letter-spacing:.3px}

/* A-frame: open */
.aframe-open{left:590px;top:96px;width:445px;height:661px}
.aframe-open .brand{top:55px}
.aframe-open .brand-name{font-size:28px}
.open-word{font-weight:300;line-height:1;letter-spacing:-1px}
.open-word.were{top:148px;font-size:84px}
.open-word.open{top:218px;font-size:96px}
.aframe-open .btn{left:125px;width:196px;height:31px;line-height:31px;font-size:15px}
.aframe-open .btn.pickup{top:340px}
.aframe-open .btn.delivery{top:505px}
.aframe-open .web{top:397px;left:0;right:0;font-size:17px}
.aframe-open .phone{top:418px;left:0;right:0;font-size:43px}
.aframe-open .tiles.upper{top:555px;left:126px;height:33px}
.aframe-open .tiles.lower{top:598px;left:124px;height:20px;gap:12px}

/* menu cover */
.menu-cover{left:227px;top:789px;width:725px;height:547px}
.menu-cover .brand{top:62px;gap:18px}
.menu-cover .brand-dot{width:28px;height:28px}
.menu-cover .brand-name{font-size:42px}
.intro{top:176px;left:85px;right:85px;text-align:center;font-size:12.5px;font-weight:300;line-height:14.5px}
.intro-note{top:226px;font-size:12px;font-weight:300}
.note-col{top:279px;width:260px;text-align:center;font-size:11.5px;font-weight:300;line-height:17px}
.note-col.left{left:115px}
.note-col.right{left:346px}
.eco{display:inline-block;width:10px;height:10px;border-radius:50%;border:1.5px solid var(--white);vertical-align:-1px}
.menu-cover .btn{top:362px;width:159px;height:26px;line-height:26px;font-size:13px}
.menu-cover .btn.pickup{left:176px}
.menu-cover .btn.delivery{left:381px}
.menu-cover .web{top:404px;left:156px;width:200px;font-size:11px}
.menu-cover .phone{top:420px;left:156px;width:200px;font-size:16px;gap:5px}
.menu-cover .tiles.upper{top:400px;left:381px;height:25px;gap:3px}
.menu-cover .tiles.lower{top:434px;left:381px;height:14px;gap:12px}
.follow{top:472px;display:flex;align-items:center;justify-content:center;gap:10px;font-size:20px;font-weight:300}
.follow .follow-gap{width:8px}
.social-square{width:18px;height:18px;background:var(--blue);border-radius:3px}

/* menu inner pages */
.menu-page{left:227px;width:725px;height:547px}
.menu-page.first{top:1368px;height:548px}
.menu-page.second{top:1954px;height:548px}
.section-title{font-family:var(--head);font-weight:700;font-size:19px;letter-spacing:.2px;text-transform:uppercase;white-space:nowrap}
.section-title::after{content:"";display:block;width:18px;height:2px;background:var(--blue);margin-top:2px}
.plain-list{list-style:none;font-size:9.5px;font-weight:300;color:var(--soft)}
.plain-list li{height:18.2px;padding-top:3px;border-bottom:1px solid var(--rule);white-space:nowrap}
.plain-list .blue{color:var(--blue)}

.starters-title{left:48px;top:32px}
.starters-list{left:48px;top:72px;width:290px}
.chips-title{left:48px;top:283px}
.chips-list{left:49px;top:321px;width:290px}
.sauces-title{left:48px;top:401px}
.sauces-list{left:49px;top:437px;width:296px}

.boxed{border:1px solid var(--soft);outline:1px solid var(--soft);outline-offset:3px}
.burgers-box{left:378px;top:27px;width:295px;height:260px}
.burgers-title{left:386px;top:32px}
.dish{width:280px;font-size:9px;font-weight:300;line-height:10.5px;color:var(--soft)}
.dish .dish-name{font-size:9.5px;color:var(--blue)}
.dish .dish-side{font-size:9.5px;color:var(--soft)}
.dish-rule{height:1px;background:var(--rule)}
.burgers .dish{left:386px}
.burgers .dish-rule{left:386px;width:278px}
.kids-title{left:375px;top:363px}
.kids-list{left:375px;top:403px;width:295px}

.fish-box{left:50px;top:27px;width:298px;height:260px}
.fish-title{left:59px;top:32px}
.fish-served{left:59px;top:67px;font-size:9px;font-weight:300;color:var(--soft)}
.fish-list{left:59px;top:82px;width:276px}
.fish-list li{height:16.6px;padding-top:2px}
.fish-prep{left:50px;width:298px;top:259px;text-align:center;font-size:9px;font-weight:300;line-height:11.5px;color:var(--soft)}
.fish-prep .blue{color:var(--blue)}
.salads-title{left:375px;top:32px}
.salads-intro{left:375px;top:70px;font-size:9px;font-weight:300;color:var(--soft)}
.salads .dish{left:375px;width:300px}
.salads .dish-rule{left:375px;width:297px}
.platters-title{left:48px;top:338px}
.platters-intro{left:48px;top:376px;width:600px;font-size:9px;font-weight:300;line-height:10px;color:var(--soft)}
.platters-list{left:48px;top:403px;width:628px}
.platters-list li{font-weight:700;font-size:9px;height:19px;padding-top:4px}
.platters-note{top:474px;font-size:9px;font-weight:300;color:var(--soft)}
</style>
</head>
<body>

<svg width="0" height="0" style="position:absolute" aria-hidden="true">
  <defs>
    <symbol id="icon-phone" viewBox="0 0 48 40">
      <path d="M2 13c0-6 10-10 22-10s22 4 22 10v3c0 1.5-1 2.5-2.5 2.5H37c-1.5 0-2.5-1-2.5-2.5v-3c-3-1-7-1.6-10.5-1.6S16.5 12 13.5 13v3c0 1.5-1 2.5-2.5 2.5H4.5C3 18.5 2 17.5 2 16z"/>
      <path d="M15 16h18l9 10v12H6V26z"/>
      <g fill="#272324"><rect x="17" y="24" width="3" height="3"/><rect x="22.5" y="24" width="3" height="3"/><rect x="28" y="24" width="3" height="3"/><rect x="17" y="29" width="3" height="3"/><rect x="22.5" y="29" width="3" height="3"/><rect x="28" y="29" width="3" height="3"/></g>
    </symbol>
    <symbol id="icon-globe" viewBox="0 0 20 20">
      <circle cx="10" cy="10" r="8.5" fill="none" stroke="currentColor" stroke-width="2"/>
      <path d="M1.5 10h17M10 1.5c-4 4.5-4 12.5 0 17M10 1.5c4 4.5 4 12.5 0 17" fill="none" stroke="currentColor" stroke-width="1.6"/>
    </symbol>
  </defs>
</svg>

<!-- A-frame: opening hours side -->
<section class="panel aframe-hours">
  <div class="brand"><span class="brand-dot"></span><span class="brand-name">Hook &amp; Harbour</span></div>
  <p class="welcome centered">WELCOME</p>
  <h1 class="open-title centered">Open Every Day</h1>
  <p class="hours lunch centered"><span class="blue">Tues – Sun</span>Lunch 12pm – 3pm</p>
  <p class="hours dinner centered"><span class="blue">Tues – Sun</span>Dinner 5pm – 9pm</p>
  <p class="services centered">Dine in <span class="pipe">|</span> Takeaway<br>Online ordering &amp; deliver<br>Fresh retail</p>
  <p class="byo centered">BYO Welcome! Wine, Beer &amp; Spirits / Soft Drinks Available</p>
  <div class="blue-rule first"></div>
  <p class="prep centered">Choose your preparation:<br>PANKO CRUMBED / TEMPURA BATTERED / GRILLED</p>
  <div class="blue-rule second"></div>
  <p class="phone"><svg width="46" height="38"><use href="#icon-phone"/></svg>3555 0142</p>
  <p class="url-pill">www.hookandharbour.com.au</p>
</section>

<!-- A-frame: we're open side -->
<section class="panel aframe-open">
  <div class="brand"><span class="brand-dot"></span><span class="brand-name">Hook &amp; Harbour</span></div>
  <p class="open-word were centered">WE’RE</p>
  <p class="open-word open centered">OPEN!</p>
  <p class="btn pickup">Order for pickup</p>
  <p class="web"><svg width="16" height="16" class="blue"><use href="#icon-globe"/></svg>www.hookandharbour.com.au</p>
  <p class="phone"><svg width="42" height="35"><use href="#icon-phone"/></svg>3555 0142</p>
  <p class="btn delivery">Order for delivery</p>
  <div class="tiles upper" role="img" aria-label="Delivery partner badges">
    <span class="tile green" style="width:32px"></span><span class="tile yellow" style="width:75px"></span><span class="tile teal" style="width:82px"></span>
  </div>
  <div class="tiles lower" role="img" aria-label="Delivery partner badges">
    <span class="tile orange" style="width:86px"></span><span class="tile red" style="width:100px"></span>
  </div>
</section>

<!-- Menu cover -->
<section class="panel menu-cover">
  <div class="brand"><span class="brand-dot"></span><span class="brand-name">Hook &amp; Harbour</span></div>
  <p class="intro">Our premium quality fish is wild caught and sustainably farmed from pristine Australian &amp; New Zealand waters, delivered in-store every day for you to enjoy! Our seafood is deep-fried to golden goodness with premium 100% Australian grown and pressed sunflower oil.</p>
  <p class="intro-note centered">(All seafood is subject to daily fresh market availability).</p>
  <p class="note-col left">Gluten friendly options are available.<br>Our takeaway packaging is <span class="eco"></span> friendly.</p>
  <p class="note-col right">Menu substitutions are not available.<br>Public holiday surcharge 15%.</p>
  <p class="btn pickup">Order for pickup</p>
  <p class="btn delivery">Order for delivery</p>
  <p class="web"><svg width="10" height="10" class="blue"><use href="#icon-globe"/></svg>www.hookandharbour.com.au</p>
  <p class="phone"><svg width="18" height="15"><use href="#icon-phone"/></svg>3555 0142</p>
  <div class="tiles upper" role="img" aria-label="Delivery partner badges">
    <span class="tile green" style="width:27px"></span><span class="tile yellow" style="width:60px"></span><span class="tile teal" style="width:66px"></span>
  </div>
  <div class="tiles lower" role="img" aria-label="Delivery partner badges">
    <span class="tile orange" style="width:68px"></span><span class="tile red" style="width:78px"></span>
  </div>
  <p class="follow">Follow us<span class="follow-gap"></span><span class="social-square"></span>hookandharbour_riverside</p>
</section>

<!-- Menu page: starters, chips, sauces, burgers, kids -->
<section class="panel menu-page first">
  <h2 class="section-title starters-title">Starters &amp; Sides</h2>
  <ul class="plain-list starters-list">
    <li>Crumbed Calamari (8)</li>
    <li>Salt &amp; Pepper Calamari (8)</li>
    <li>Crumbed Sea Scallop</li>
    <li>Crumbed Prawn</li>
    <li>BBQ Prawn Skewer</li>
    <li>Onion Rings (8)</li>
    <li>Popcorn Chicken</li>
    <li>Potato Scallop</li>
    <li>Grilled Halloumi (3 slices)</li>
    <li>Fried Halloumi (3 slices, crumbed)</li>
  </ul>
  <h2 class="section-title chips-title">Chips</h2>
  <ul class="plain-list chips-list">
    <li>Chips GF</li>
    <li>Beer Battered Chips</li>
    <li>Sweet Potato Chips</li>
  </ul>
  <h2 class="section-title sauces-title">Sauces</h2>
  <ul class="plain-list sauces-list">
    <li>Tartare, Aioli, Tomato &amp; Chipotle Mayonnaise</li>
  </ul>

  <div class="boxed burgers-box"></div>
  <h2 class="section-title burgers-title">Burgers &amp; Tacos</h2>
  <div class="burgers">
    <p class="dish" style="position:absolute;top:76px"><span class="dish-name">Fish Burger</span> <span class="dish-side">&amp; chips</span><br>Crumbed cod fillet, shredded lettuce, tomato &amp; tartare sauce in a toasted bun.</p>
    <div class="dish-rule" style="position:absolute;top:117px"></div>
    <p class="dish" style="position:absolute;top:127px"><span class="dish-name">Fish Tacos</span> <span class="dish-side">(3) &amp; chips</span><br>Beer battered cod, shredded red &amp; green cabbage, carrot, chipotle mayonnaise in soft flour tortillas.</p>
    <div class="dish-rule" style="position:absolute;top:172px"></div>
    <p class="dish" style="position:absolute;top:183px"><span class="dish-name">Chicken Burger</span> <span class="dish-side">&amp; chips</span><br>Grilled free range chicken tenders, shredded lettuce, tomato, cheese, avocado, aioli in a toasted bun.</p>
    <div class="dish-rule" style="position:absolute;top:228px"></div>
    <p class="dish" style="position:absolute;top:239px"><span class="dish-name">Steak Burger</span> <span class="dish-side">&amp; chips</span><br>Grilled grass fed rib fillet, shredded lettuce, tomato, cheese, caramelised onion, BBQ sauce in a toasted bun.</p>
  </div>

  <h2 class="section-title kids-title">Children’s Fish &amp; Chips</h2>
  <ul class="plain-list kids-list">
    <li><span class="blue">Fish Fingers</span> (4) &amp; chips</li>
    <li><span class="blue">Crumbed Calamari</span> (4) &amp; chips</li>
    <li><span class="blue">Popcorn Chicken</span> &amp; chips</li>
  </ul>
</section>

<!-- Menu page: fish & chips, salads, platters -->
<section class="panel menu-page second">
  <div class="boxed fish-box"></div>
  <h2 class="section-title fish-title">Fish &amp; Chips</h2>
  <p class="fish-served">Served with your choice of chips, tartare sauce &amp; lemon.</p>
  <ul class="plain-list fish-list">
    <li><span class="blue">Cod</span> &amp; chips (NZ, wild caught)</li>
    <li><span class="blue">Whiting</span> &amp; chips (QLD, wild caught, crumbed only)</li>
    <li><span class="blue">Flathead</span> &amp; chips (SA, wild caught, beer battered only)</li>
    <li><span class="blue">Snapper</span> &amp; chips (NT, wild caught)</li>
    <li><span class="blue">Barramundi</span> &amp; chips (NT, ocean farmed)</li>
    <li><span class="blue">Salmon</span> &amp; chips (TAS, ocean farmed)</li>
    <li><span class="blue">Crumbed Calamari</span> (8) &amp; chips</li>
    <li><span class="blue">Salt &amp; Pepper Calamari</span> (8) &amp; chips</li>
    <li><span class="blue">Crumbed Prawns</span> (5) &amp; chips</li>
    <li><span class="blue">BBQ Prawn Skewers</span> (5) &amp; chips</li>
  </ul>
  <p class="fish-prep"><span class="blue">Made fresh to order</span> | Choose your preparation:<br>GRILLED / CRUMBED / BEER BATTERED</p>

  <h2 class="section-title salads-title">Salads</h2>
  <p class="salads-intro">Freshly prepared to order using local produce.</p>
  <div class="salads">
    <p class="dish" style="position:absolute;top:105px"><span class="dish-name">Greek</span></p>
    <div class="dish-rule" style="position:absolute;top:118px"></div>
    <p class="dish" style="position:absolute;top:121px">Lettuce, cucumber, tomato, red onion, Kalamata olives, feta, Greek peppers, wild oregano, dressed in Greek extra virgin olive oil vinaigrette.</p>
    <p class="dish" style="position:absolute;top:158px"><span class="dish-name">Roast Pumpkin</span></p>
    <div class="dish-rule" style="position:absolute;top:171px"></div>
    <p class="dish" style="position:absolute;top:174px">Roast pumpkin, wild rocket, Parmigiano Reggiano, toasted pine nuts, dressed in Greek extra virgin olive oil &amp; vintage balsamic vinegar.</p>
    <p class="dish" style="position:absolute;top:211px"><span class="dish-name">Slaw</span></p>
    <div class="dish-rule" style="position:absolute;top:224px"></div>
    <p class="dish" style="position:absolute;top:227px">Shredded red &amp; green cabbage, carrot, tossed in a light mayonnaise dressing.</p>
    <p class="dish" style="position:absolute;top:256px"><span class="dish-name">Asian Slaw</span></p>
    <div class="dish-rule" style="position:absolute;top:269px"></div>
    <p class="dish" style="position:absolute;top:272px">Shredded red &amp; green cabbage, carrot, spring onion, crispy noodles, sesame seeds, tossed in a sweet soy dressing.</p>
  </div>

  <h2 class="section-title platters-title">Cooked Seafood Platters</h2>
  <p class="platters-intro">Cooked Seafood Platters include: whiting, calamari, salt &amp; pepper calamari, prawns, sea scallops, chips, one of our freshly made salads, tartare sauce &amp; lemon.</p>
  <ul class="plain-list platters-list">
    <li>Cooked Platter for One</li>
    <li>Cooked Platter for Two</li>
    <li>Cooked Platter for Three</li>
  </ul>
  <p class="platters-note centered">Our seafood platters are available crumbed only.</p>
</section>

</body>
</html>
```